Company Creation Website Redesign

Firmora88 is an Australian company creation website that specialises in creating company and trust documents. Our website was created in 2014 and we would like a new fresh look. We would like to maintain the same colour scheme of light blue and white. We feel the current landing page is a bit busy and would like something cleaner and more minimalist.

We would like all toolbar options to be the same but redesigned with better font, more aesthetically pleasing etc.

The website is built on AngularJS framework with HTML/CSS markup.

Please have a look at the current landing page.
firmora88.com.au

Target Market(s)

Accountants, those want to create company

Industry/Entity Type

Commerce

Coding

Coded - Design and coding required

Number of Pages Required

5+ page

Font styles to use
Sans Serif

Colors
0054AA
0677BA
7BADD7
CADEEF
E8F1F8

Requirements
Must have
• Attractive symbols
Nice to have
• Simple colour scheme
Should not have
• Busy images

```html
<!DOCTYPE html>
<html lang="en">
<head>
<meta charset="utf-8">
<title>Firmora88 – Australian Online Company Registration</title>
<link rel="stylesheet" href="https://fonts.googleapis.com/css2?family=Rubik:wght@500;700&family=Roboto:ital,wght@0,400;0,500;0,700;1,500&display=swap">
<style>
:root{
  --blue:#1f74d0;
  --blue-dark:#0054aa;
  --blue-band:#2f7fd3;
  --blue-pale:#e4f0fb;
  --red:#e31b23;
  --green:#8cc21e;
  --ink:#111;
  --text:#333;
  --muted:#666;
  --line:#dfe3e8;
  --footer:#121212;
  --white:#fff;
}
*{box-sizing:border-box;margin:0;padding:0}
html,body{width:1200px;height:4573px;overflow:hidden}
body{position:relative;font-family:Roboto,Arial,sans-serif;color:var(--text);background:var(--white)}
.abs{position:absolute}
.head{font-family:Rubik,Arial,sans-serif;font-weight:700;color:var(--ink)}
.btn{position:absolute;display:flex;align-items:center;justify-content:center;gap:10px;color:#fff;font-family:Roboto,sans-serif;font-weight:700;font-size:14px;border-radius:3px;text-transform:uppercase}
.btn .dot{width:13px;height:13px;border-radius:50%;background:#fff;display:inline-block;position:relative}
.btn .dot::after{content:"";position:absolute;left:4px;top:3px;border-left:5px solid var(--blue);border-top:3.5px solid transparent;border-bottom:3.5px solid transparent}
.btn.red .dot::after{border-left-color:var(--red)}
.btn.green .dot::after{border-left-color:var(--green)}
.blue{background:var(--blue)}.red{background:var(--red)}.green{background:var(--green)}
.ph{position:absolute}
.section-title{position:absolute;left:0;width:1200px;text-align:center;font-size:30px}
.section-title span{border-left:5px solid var(--blue);padding-left:10px}

/* header */
.topbar{top:0;left:0;width:1200px;height:6px;background:var(--blue)}
.logo{display:flex;align-items:center;gap:10px;font-family:Roboto,sans-serif;font-weight:500;font-size:22px;color:var(--blue-dark)}
.logo i{width:26px;height:26px;background:var(--blue);border-radius:4px;display:block}
.info{display:flex;align-items:center;gap:10px;font-size:14px;font-weight:700;color:var(--ink);line-height:1.3}
.info small{font-size:12px;font-weight:700}
.circ{width:34px;height:34px;border-radius:50%;background:var(--blue);display:flex;align-items:center;justify-content:center}
.search{top:30px;left:595px;width:195px;height:38px;border:1px solid var(--line);font-size:13px;color:#888;padding:11px 12px}
.search b{position:absolute;right:-1px;top:-1px;width:38px;height:38px;background:var(--blue);display:flex;align-items:center;justify-content:center}
.nav{top:98px;left:0;width:1200px;height:56px;border-top:1px solid var(--line);border-bottom:1px solid var(--line)}
.nav ul{list-style:none;display:flex;align-items:center;height:100%;padding-left:97px;font-size:14px;color:var(--ink);font-weight:500}
.nav li{padding:0 18px;height:100%;display:flex;align-items:center;gap:8px}
.nav li.active{background:var(--blue);color:#fff;padding:0 24px}
.caret{border-top:5px solid var(--ink);border-left:4px solid transparent;border-right:4px solid transparent}

/* hero */
.hero{top:176px;left:0;width:1200px;height:610px;background:linear-gradient(135deg,#8a8f96,#5f6670 45%,#474d55)}
.hero h1{position:absolute;top:252px;left:0;width:1200px;text-align:center;color:#fff;font-size:36px;line-height:1.15;font-family:Rubik,sans-serif;font-weight:700}
.hero p{position:absolute;top:352px;width:1200px;text-align:center;color:#fff;font-size:18px}
.arrow{position:absolute;top:356px;width:38px;height:38px;border:2px solid #fff;border-radius:50%}
.formcard{top:719px;left:108px;width:982px;height:124px;background:#fff;border-radius:6px;box-shadow:0 6px 18px rgba(0,0,0,.13)}
.field{position:absolute;top:36px;width:180px;height:50px;background:#f1f2f4;border:1px solid #d8dbe0;font-size:14px;color:#555;padding:16px 15px}

/* welcome */
.welcome-card{top:989px;left:541px;width:569px;height:417px;background:#fff;box-shadow:0 4px 20px rgba(0,0,0,.1);padding:42px 58px}
.welcome-card h2{font-size:29px;border-left:5px solid var(--blue);padding-left:14px;line-height:1}
.welcome-card .lead{margin-top:24px;color:var(--blue);font-size:15px;line-height:1.55}
.welcome-card .body{margin-top:14px;font-size:14px;line-height:1.85;color:var(--ink)}

/* trust band */
.trust{top:1496px;left:0;width:1200px;height:450px;background:var(--blue-pale)}
.trust h2{position:absolute;top:88px;left:112px;font-size:30px;line-height:1.3}
.trust h2 span{border-left:5px solid var(--blue);padding-left:12px}

/* why */
.why-card{position:absolute;top:2121px;width:305px;height:394px}
.why-card .photo{position:absolute;top:54px;left:0;width:305px;height:200px}
.why-card .box{position:absolute;top:230px;left:12px;width:281px;height:164px;background:#fff;box-shadow:0 2px 10px rgba(0,0,0,.12);text-align:center;padding:22px 20px}
.why-card h3{font-size:14px;font-weight:700;color:var(--ink);line-height:1.35}
.why-card p{font-size:14px;color:var(--muted);line-height:1.75;margin-top:6px}
.why-card a{display:block;margin-top:8px;font-size:14px;font-weight:700;color:var(--blue);text-decoration:underline}
.why-card .icon{position:absolute;top:0;left:100px;width:104px;height:104px;border-radius:50%;background:var(--blue);border:6px solid #fff;box-shadow:0 0 0 2px #cfe0f3;display:flex;align-items:center;justify-content:center}

/* band */
.band{top:2602px;left:0;width:1200px;height:272px;background:var(--blue-band)}
.band h2{position:absolute;top:52px;width:1200px;text-align:center;color:#fff;font-size:30px;line-height:1.25}

/* reviews */
.review{position:absolute;top:3035px;width:314px;height:235px;border:1px solid var(--line);border-radius:10px;text-align:center;padding:22px 18px}
.review .q{font-family:Georgia,serif;font-size:56px;line-height:40px;height:36px;color:var(--blue);font-weight:700}
.review p{font-size:14px;line-height:1.7;color:#444;margin-top:8px}
.review .stars{color:#f4b400;font-size:16px;letter-spacing:2px;margin-top:4px}
.avatar{position:absolute;top:3302px;width:80px;height:80px;border-radius:50%;background:linear-gradient(#c9d3dd,#8f9aa6)}
.avatar i{position:absolute;right:-4px;bottom:2px;width:26px;height:26px;border-radius:50%;background:#fff;border:2px solid var(--line)}
.rname{position:absolute;top:3398px;width:314px;text-align:center;font-size:15px;font-weight:700;color:var(--blue)}

/* news */
.news{top:3500px;left:0;width:1200px;height:650px;background:var(--blue-pale)}
.news-card{position:absolute;background:#fff;box-shadow:0 2px 8px rgba(0,0,0,.08)}
.news-card h4{font-size:14px;font-weight:700;color:var(--ink);line-height:1.3;text-transform:uppercase}
.meta{font-size:14px;color:var(--blue);margin:8px 0;display:flex;gap:24px}
.news-card p{font-size:14px;line-height:1.8;color:#333}
.more{font-size:14px;font-weight:700;color:var(--blue);margin-top:8px;display:flex;align-items:center;gap:10px}
.more .d{width:14px;height:14px;border-radius:50%;background:var(--blue)}

/* footer */
.footer{top:4150px;left:0;width:1200px;height:423px;background:var(--footer);color:#fff}
.footer h5{position:absolute;font-size:14px;font-weight:700;text-transform:uppercase}
.footer ul{position:absolute;list-style:none;font-size:14px;line-height:39px}
.footer ul li::before{content:"» ";margin-right:8px}
.ficon{position:absolute;width:32px;height:32px;border-radius:50%;background:#fff}
.fsoc{width:28px;height:28px;border-radius:50%;border:1.5px solid #fff;display:inline-block;margin-right:10px}
</style>
</head>
<body>

<!-- header -->
<div class="abs topbar"></div>
<div class="abs logo" style="top:32px;left:110px"><i></i>Firmora88</div>
<div class="abs info" style="top:30px;left:292px">
  <span class="circ"><svg width="18" height="18" viewBox="0 0 24 24" fill="#fff"><path d="M12 3a8 8 0 0 0-8 8v5h4v-6H6a6 6 0 0 1 12 0h-2v6h4v-5a8 8 0 0 0-8-8z"/></svg></span>
  <span>Customer<br>Service 24/7</span>
</div>
<div class="abs info" style="top:30px;left:440px">
  <span class="circ"><svg width="18" height="18" viewBox="0 0 24 24" fill="#fff"><path d="M6.6 10.8a15 15 0 0 0 6.6 6.6l2.2-2.2c.3-.3.7-.4 1-.2 1.1.4 2.3.6 3.6.6.6 0 1 .4 1 1V20c0 .6-.4 1-1 1A17 17 0 0 1 3 4c0-.6.4-1 1-1h3.5c.6 0 1 .4 1 1 0 1.3.2 2.5.6 3.6.1.3 0 .7-.2 1z"/></svg></span>
  <span><small>CALL US</small><br>03 9000 4417</span>
</div>
<div class="abs search">Search<b><svg width="16" height="16" viewBox="0 0 24 24" fill="none" stroke="#fff" stroke-width="3"><circle cx="10" cy="10" r="6"/><path d="M15 15l5 5"/></svg></b></div>
<div class="btn blue" style="top:28px;left:808px;width:114px;height:42px">Login</div>
<div class="btn red" style="top:28px;left:938px;width:150px;height:42px">Register now</div>
<nav class="abs nav"><ul>
  <li class="active">HOME</li>
  <li>REGISTERCOMPANY <span class="caret"></span></li>
  <li>BUSINESSNAME <span class="caret"></span></li>
  <li>SET UPTRUST <span class="caret"></span></li>
  <li>SET UPBUSINESSPLAN</li>
  <li>SMSF</li>
  <li>MORE <span class="caret"></span></li>
  <li>CONTACT</li>
</ul></nav>

<!-- hero -->
<section class="abs hero" role="img" aria-label="Business people shaking hands in a modern office">
  <h1>AUSTRALIAN ONLINE COMPANY<br>REGISTRATION</h1>
  <p>Simple, quick and trusted service in 3 easy online steps</p>
  <div class="btn red" style="top:394px;left:518px;width:165px;height:44px">Get started <span class="dot"></span></div>
  <span class="arrow" style="left:38px"></span>
  <span class="arrow" style="left:1124px"></span>
</section>
<form class="abs formcard">
  <div class="field" style="left:54px">Name:</div>
  <div class="field" style="left:244px">Email:</div>
  <div class="field" style="left:432px">Address:</div>
  <div class="field" style="left:622px">Message:</div>
  <div class="btn blue" style="top:36px;left:812px;width:117px;height:50px">Submit</div>
</form>

<!-- welcome -->
<div class="ph" style="top:934px;left:89px;width:503px;height:433px;background:linear-gradient(135deg,#cfd8e0,#8c98a6)" role="img" aria-label="Two colleagues reviewing a document at a laptop"></div>
<article class="abs welcome-card">
  <h2 class="head">WELCOME TO FIRMORA88</h2>
  <p class="lead">Advanced, automated and simple company registration<br>24 hours a day.</p>
  <p class="body">We offer a fully automated, quick and cost effective company registration process. By completing an easy form, within 5 minutes you will receive full company registration documents setting up an Australian private company. We offer full of the customer support (telephone and email) 24 hours a day. It could not be any simpler, register your company today.</p>
  <div class="btn blue" style="top:324px;left:58px;width:160px;height:52px">Learn more <span class="dot"></span></div>
</article>

<!-- trust -->
<section class="abs trust">
  <div class="ph" style="top:0;left:480px;width:720px;height:450px;background:linear-gradient(90deg,rgba(228,240,251,0),#b9c6d3 30%,#5a6470)" role="img" aria-label="Group of business professionals with a woman holding a clipboard"></div>
  <h2 class="head"><span>QUICK, SIMPLE</span><br>DISCRETIONARY AND UNIT<br>TRUST REGISTRATION</h2>
  <p class="abs" style="top:216px;left:112px;font-size:20px;color:var(--ink)">Completed in 3 easy steps for</p>
  <p class="abs head" style="top:256px;left:112px;font-size:30px"><span style="color:var(--blue)">$129</span> (EXC GST).</p>
  <div class="btn blue" style="top:312px;left:112px;width:150px;height:46px">Apply now <span class="dot"></span></div>
</section>

<!-- why -->
<h2 class="section-title head" style="top:2028px"><span>WHY USE US</span></h2>
<div class="why-card" style="left:107px">
  <div class="photo" style="background:linear-gradient(135deg,#d8c8b4,#8a7560)" role="img" aria-label="Team celebrating around a table"></div>
  <div class="icon"><svg width="44" height="44" viewBox="0 0 24 24" fill="#fff"><circle cx="12" cy="6" r="3"/><circle cx="5" cy="9" r="2"/><circle cx="19" cy="9" r="2"/><path d="M6 20v-4a6 6 0 0 1 12 0v4z"/></svg></div>
  <div class="box"><h3>THE BEST PRICE TO REGISTER<br>A COMPANY IN AUSTRALIA!</h3><p>We charge only $44 + GST which<br>is the cheapest in Australia.</p><a>READ MORE</a></div>
</div>
<div class="why-card" style="left:447px">
  <div class="photo" style="background:linear-gradient(135deg,#cdd3d9,#6d7680)" role="img" aria-label="Two men discussing paperwork in an office"></div>
  <div class="icon"><svg width="44" height="44" viewBox="0 0 24 24" fill="#fff"><circle cx="12" cy="5" r="3"/><rect x="10" y="9" width="4" height="4"/><circle cx="5" cy="15" r="2.5"/><circle cx="19" cy="15" r="2.5"/><path d="M1 22a4 4 0 0 1 8 0zM15 22a4 4 0 0 1 8 0zM8 22a4 4 0 0 1 8 0z"/></svg></div>
  <div class="box"><h3>SOLICITOR PREPARED LEGAL<br>DOCUMENTS</h3><p>All our legal documents are<br>prepared by experienced commercial</p><a>READ MORE</a></div>
</div>
<div class="why-card" style="left:787px">
  <div class="photo" style="background:linear-gradient(135deg,#d4d9de,#7b838c)" role="img" aria-label="Business team looking at a tablet"></div>
  <div class="icon"><svg width="44" height="44" viewBox="0 0 24 24" fill="#fff"><circle cx="9" cy="7" r="3.5"/><path d="M3 21v-4a6 6 0 0 1 12 0v4z"/><circle cx="18" cy="7" r="3" fill="none" stroke="#fff" stroke-width="1.5"/></svg></div>
  <div class="box"><h3>SIMPLE ONLINE COMPANY<br>APPLICATION FORM</h3><p>Easy to follow and complete<br>application form ensuring fastest</p><a>READ MORE</a></div>
</div>

<!-- update band -->
<section class="abs band">
  <h2 class="head" style="color:#fff">UPDATE YOUR COMPANY CHANGES<br>TO THE REGISTRY FOR JUST $60</h2>
  <div class="btn red" style="top:158px;left:332px;width:258px;height:50px">Customer service 24/7 <svg width="16" height="16" viewBox="0 0 24 24" fill="#fff"><rect x="3" y="5" width="18" height="16" rx="2"/><rect x="5" y="9" width="14" height="10" fill="#e31b23"/></svg></div>
  <div class="btn green" style="top:158px;left:598px;width:270px;height:50px">Update company details <span class="dot"></span></div>
</section>

<!-- reviews -->
<h2 class="section-title head" style="top:2962px"><span>OUR REVIEW</span></h2>
<div class="review" style="left:103px"><div class="q">“</div><p>Nadia is very helpful, amazing customer service,caring professional and knowledgeable. I couldn't recommend Firmora88 highly enough. Nadia did a trademark my logo and I am super happy. keep this beautiful job up!!</p><div class="stars">★★★★★</div></div>
<div class="review" style="left:443px"><div class="q">“</div><p>Elliot and Nadia were simply fantastic. I needed to set up a trust urgently and they were there to help every step of the way. Thank you so much for your outstanding service and I will most certainly be back!</p><div class="stars">★★★★★</div></div>
<div class="review" style="left:783px"><div class="q">“</div><p>I couldn't recommend Firmora88 highly enough! Registered a trust with corporate trustee and the confirmations and registrations came through so quickly I was amazed. They made everything so easy! Everything just ready to sign!</p><div class="stars">★★★★★</div></div>
<div class="avatar" style="left:220px" role="img" aria-label="Reviewer portrait"><i></i></div>
<div class="avatar" style="left:560px" role="img" aria-label="Reviewer portrait"><i></i></div>
<div class="avatar" style="left:900px" role="img" aria-label="Reviewer portrait"><i></i></div>
<div class="rname" style="left:103px">RAVI TANDON</div>
<div class="rname" style="left:443px">MEI TRAN</div>
<div class="rname" style="left:783px">THETIDYTRADER</div>

<!-- news -->
<section class="abs news">
  <h2 class="section-title head" style="top:56px"><span>LATEST NEWS</span></h2>
  <article class="news-card" style="top:130px;left:108px;width:427px;height:460px">
    <div class="ph" style="top:10px;left:10px;width:407px;height:205px;background:linear-gradient(135deg,#c9cfd6,#6f7985)" role="img" aria-label="Team working together on laptops"></div>
    <div class="abs" style="top:242px;left:27px;width:380px">
      <h4>Be aware of trademark scam and<br>false billing</h4>
      <div class="meta"><span>◷ 01:13</span><span>▦ 2018/08/16</span></div>
      <p>In this year, we often see an increase reports of false billing and unsolicited invoices being sent to our trade mark applicants.Once you apply for an IP right</p>
      <div class="btn blue" style="top:170px;left:0;width:152px;height:44px">Learn more <span class="dot"></span></div>
    </div>
  </article>
  <article class="news-card" style="top:130px;left:548px;width:544px;height:223px">
    <div class="ph" style="top:0;left:0;width:214px;height:223px;background:linear-gradient(135deg,#cbd1d8,#737d88)" role="img" aria-label="Colleagues discussing a business plan"></div>
    <div class="abs" style="top:30px;left:244px;width:280px">
      <h4>What is a business plan and<br>why do you need it ?</h4>
      <div class="meta"><span>◷ 12:53</span><span>▦ 2018/08/16</span></div>
      <p>A Business plan outlines how you intended to run your business or company, and build its own core value</p>
      <div class="more">LEARN MORE <span class="d"></span></div>
    </div>
  </article>
  <article class="news-card" style="top:363px;left:548px;width:544px;height:227px">
    <div class="ph" style="top:0;left:0;width:214px;height:227px;background:linear-gradient(135deg,#d2c3b0,#7f6f5e)" role="img" aria-label="Business meeting around a tablet"></div>
    <div class="abs" style="top:26px;left:234px;width:290px">
      <h4>How to be a victim of your own<br>success by failing to trade mark</h4>
      <div class="meta"><span>◷ 04:12</span><span>▦ 2018/01/15</span></div>
      <p>Didn't trade mark your brand? You now run the risk of someone else using your brand and associating you business's</p>
      <div class="more">LEARN MORE <span class="d"></span></div>
    </div>
  </article>
</section>

<!-- footer -->
<footer class="abs footer">
  <div class="abs logo" style="top:70px;left:112px;color:#fff"><i></i>Firmora88</div>
  <p class="abs" style="top:140px;left:112px;width:300px;font-size:13px;line-height:1.8">We offer a fully automated, quick and cost effective company registration process.</p>
  <h5 style="top:206px;left:112px">Follow us</h5>
  <div class="abs" style="top:230px;left:112px;width:40px;height:3px;background:var(--blue)"></div>
  <div class="abs" style="top:256px;left:112px"><span class="fsoc"></span><span class="fsoc"></span><span class="fsoc"></span><span class="fsoc"></span></div>

  <h5 style="top:56px;left:472px">Quick links</h5>
  <div class="abs" style="top:80px;left:472px;width:40px;height:3px;background:var(--blue)"></div>
  <ul style="top:94px;left:472px"><li>Home</li><li>Registercompany</li><li>Businessname</li><li>Set Uptrust</li><li>More ▾</li><li>Contact</li></ul>

  <h5 style="top:56px;left:700px">Other links</h5>
  <div class="abs" style="top:80px;left:700px;width:40px;height:3px;background:var(--blue)"></div>
  <ul style="top:94px;left:700px"><li>FAQ</li><li>Services</li><li>Team</li><li>Privacy</li><li>Policy</li></ul>

  <h5 style="top:56px;left:887px">Contact us</h5>
  <div class="abs" style="top:80px;left:887px;width:40px;height:3px;background:var(--blue)"></div>
  <span class="ficon" style="top:113px;left:887px"></span>
  <p class="abs" style="top:108px;left:935px;font-size:13px;line-height:1.8"><b style="font-size:12px">Phone Number :</b><br>03 9000 4417</p>
  <span class="ficon" style="top:183px;left:887px"></span>
  <p class="abs" style="top:178px;left:935px;font-size:13px;line-height:1.8"><b style="font-size:12px">Email:</b><br>info@firmora88.com.au</p>
  <span class="ficon" style="top:250px;left:887px"></span>
  <p class="abs" style="top:245px;left:935px;width:170px;font-size:13px;line-height:1.8"><b style="font-size:12px">Address :</b><br>5,Lorem ipsum dolor sit consectetur adipiscing sed do admit eiusmod.</p>

  <div class="abs" style="top:375px;left:112px;width:976px;height:1px;background:#333"></div>
  <p class="abs" style="top:392px;left:0;width:1200px;text-align:center;font-size:13px">©Copyrights 2022 Firmora88 All Rights Reserved.</p>
</footer>

</body>
</html>
```